Web page for a garment manufacturing company

We are clothing manufacturer based in Romania.
With our recent expansion, we have significantly increased our internal capacity, allowing us to take on new partnerships and deliver high-quality production services.
Our expertise includes producing classic coats, blazers, trousers, skirts, dresses, and blouses, though we are flexible and open to working with various other textile products.

Target Market(s)

High-end market and luxury

Industry/Entity Type

Garments Manufacturer

Coding

Coded - Design and coding required

Number of Pages Required

1 page

Colors

Designer to choose only greyscale colors for use in the design.

Requirements
Must have
• Velmora logo from our presentation
Nice to have
• https://www.lorvani.pt/
Should not have
• prices, wedding dresses, collections

```html
<!DOCTYPE html>
<html lang="en">
<head>
<meta charset="utf-8">
<title>Velmora — Premium Clothing Manufacturing</title>
<link href="https://fonts.googleapis.com/css2?family=Figtree:wght@300;400;500&family=Tinos&display=swap" rel="stylesheet">
<style>
:root{
  --ink:#1f2226;
  --dark:#23262b;
  --text:#2b2b2b;
  --muted:#9a9a9a;
  --line:#e4e4e4;
  --card:#ffffff;
  --page:#ffffff;
  --soft:#f4f4f4;
}
*{box-sizing:border-box;margin:0;padding:0}
html,body{width:1200px;height:4451px;overflow:hidden;background:var(--page)}
body{font-family:'Figtree',sans-serif;color:var(--ink);position:relative}
.abs{position:absolute}
.serif{font-family:'Tinos',serif}
p.body{font-family:'Tinos',serif;color:var(--muted);font-size:12.5px;line-height:1.75}
h2{font-weight:400;font-size:40px;line-height:1.35;color:var(--ink)}
.photo{position:absolute;overflow:hidden}
/* nav */
.nav{left:107px;top:0;width:986px;height:69px;border-bottom:1px solid var(--line);display:flex;align-items:center}
.brand{font-size:24px;font-weight:300;color:#7a7a7a;letter-spacing:-.5px}
.nav ul{list-style:none;display:flex;gap:20px;margin-left:auto;font-size:11.5px;margin-right:28px}
.lang{display:flex;align-items:center;gap:7px;font-size:11.5px;margin-right:26px}
.btn-outline{border:1px solid var(--line);border-radius:22px;padding:11px 26px;font-size:11.5px}
/* hero */
.hero{left:107px;top:97px;width:986px;height:500px;background:linear-gradient(160deg,#5a5d60,#2b2d30 55%,#454545)}
.hero h1{position:absolute;left:54px;top:170px;font-weight:400;font-size:49px;line-height:1.33;color:#fff;width:820px}
.hero p{position:absolute;left:54px;top:310px;color:#eee;font-size:13px}
/* about */
.about-text{left:107px;top:650px;width:490px}
.btn-dark{display:inline-block;background:var(--dark);color:#fff;border-radius:22px;padding:14px 26px;font-size:11.5px}
.stats{left:107px;top:1063px;display:flex;gap:38px}
.stat b{display:block;font-weight:400;font-size:50px;line-height:1.1}
.stat span{font-family:'Tinos',serif;font-size:12px;color:#555}
/* cards */
.grid{display:grid;grid-template-columns:repeat(3,320px);gap:14px}
.card{background:var(--card);box-shadow:0 0 0 1px #f0f0f0;padding:20px 20px}
.card h3{font-weight:400;font-size:25px;line-height:1.4;margin-bottom:14px}
.card.dark{background:var(--dark);color:#fff}
.card.dark p.body{color:#cfcfcf}
.icon{width:22px;height:22px;margin-bottom:16px}
/* certs */
.certs{left:107px;top:1780px;width:986px;text-align:center}
.badge-row{display:flex;justify-content:center;align-items:center;gap:30px;margin-top:30px}
.badge{background:#d9d9d9}
/* tour */
.tour-band{left:0;top:2184px;width:510px;height:365px;background:var(--dark)}
.caption{background:#fff;font-size:25px;padding:0 14px;display:flex;align-items:center}
/* community */
.captions{display:flex;gap:14px;font-size:26px}
/* form */
label{display:block;font-size:9px;margin-bottom:6px}
.field{border:1px solid #cfcfcf;border-radius:22px;height:40px;padding:0 14px;font-size:11.5px;display:flex;align-items:center;color:#aaa}
/* footer */
.footer{left:0;top:4129px;width:1200px;height:322px;background:var(--dark);color:#fff}
.footer .sm{font-size:11.5px;line-height:1.6}
.footer h4{font-weight:400;font-size:19px;margin-bottom:16px}
.flag{display:inline-block;width:24px;height:16px;margin-left:6px;vertical-align:middle}
</style>
</head>
<body>

<header class="abs nav">
  <div class="brand">Velmora</div>
  <ul><li>About Us</li><li>Strong Value</li><li>Expertise</li><li>Get in Touch</li></ul>
  <div class="lang"><span class="flag" style="background:#1d2a5a;margin:0"></span>EN
    <svg width="10" height="6" viewBox="0 0 10 6"><path d="M1 1l4 4 4-4" fill="none" stroke="#333" stroke-width="1.2"/></svg></div>
  <div class="btn-outline">Contact Us</div>
</header>

<section class="abs hero" role="img" aria-label="Photo of professionals in tailored coats walking past stone columns">
  <h1>Your Vision, Our Craft – Premium Clothing Manufacturing Solutions</h1>
  <p class="serif">From concept to creation, we deliver high-quality apparel production for brands of all sizes.</p>
</section>

<section class="abs about-text">
  <h2 style="width:420px">Where Fashion Meet Quality</h2>
  <p class="body" style="margin-top:22px">VELMORA is a manufacturing company for Ready to wear, situated in Brăila, a city with a rich tradition in the clothing industry. The top management is international, and we are proud to have a diverse and dynamic group of professionals from different countries working together.</p>
  <p class="body" style="margin-top:12px">With our optimistic team spirit and passion for high quality productions, we are ready to take on new challenges and delight our clients with very good results.</p>
  <div class="btn-dark" style="margin-top:28px">Contact Us</div>
</section>
<div class="abs stats">
  <div class="stat"><b>19</b><span>Years of Experience</span></div>
  <div class="stat"><b>5k</b><span>Active Worker</span></div>
  <div class="stat"><b>100k</b><span>Pieces per Month</span></div>
</div>
<div class="photo" style="left:607px;top:650px;width:486px;height:502px;background:linear-gradient(180deg,#8fa0ad 0%,#b6c2ca 35%,#5a4a44 60%,#2e2a28 100%)" role="img" aria-label="Photo of the factory building with the company name on its facade and an established 2005 seal"></div>

<section class="abs" style="left:107px;top:1212px">
  <div class="grid">
    <div style="padding-top:8px"><h2 style="font-size:40px">Our<br>Strong<br>Value</h2></div>
    <div class="card dark" style="height:249px"><h3>Prioritize Worker Well-Being</h3><p class="body">Implement policies and initiatives that support the physical and mental well being of our workers, ensuring fair wages, safe working conditions, and opportunities for professional growth and personal development.</p></div>
    <div class="card" style="height:249px"><h3>High Quality Products and Services</h3><p class="body">Continuously improve our products and services, focusing on exceptional quality, durability, and customer satisfaction.</p></div>
    <div class="card" style="height:250px"><h3>Environmental Responsibility</h3><p class="body">Minimize our environmental impact by adopting sustainable practices throughout our supply chain, including responsible sourcing, reducing waste, and promoting recycling and energy efficiency.</p></div>
    <div class="card" style="height:250px"><h3>Social Responsibility</h3><p class="body">Actively engage in initiatives that contribute to the well being of communities we operate in, supporting local causes and organizations.</p></div>
    <div class="card" style="height:250px"><h3>Innovation and Technology</h3><p class="body">Embrace innovation and leverage technology to streamline operations, enhance customer experience, and develop sustainable solutions that address evolving market demands.</p></div>
  </div>
</section>

<section class="abs certs" aria-label="Certification badges">
  <h2>Certifications</h2>
  <div class="badge-row">
    <div class="badge" style="width:70px;height:70px;border-radius:50%"></div>
    <div class="badge" style="width:70px;height:70px;border-radius:50%"></div>
    <div class="badge" style="width:70px;height:70px;border-radius:50%"></div>
    <div class="badge" style="width:180px;height:44px;border-radius:6px"></div>
    <div class="badge" style="width:240px;height:70px;border-radius:6px"></div>
  </div>
  <div class="badge-row" style="gap:28px;margin-top:22px">
    <div class="badge" style="width:80px;height:80px;border-radius:50%"></div>
    <div class="badge" style="width:190px;height:80px;border-radius:40px"></div>
    <div class="badge" style="width:80px;height:80px;border-radius:50%"></div>
    <div class="badge" style="width:80px;height:80px;border-radius:50%"></div>
    <div class="badge" style="width:80px;height:80px;border-radius:50%"></div>
    <div class="badge" style="width:80px;height:80px;border-radius:50%"></div>
    <div class="badge" style="width:80px;height:80px;border-radius:50%"></div>
  </div>
  <div class="badge-row" style="margin-top:16px">
    <div class="badge" style="width:54px;height:84px;border-radius:4px"></div>
    <div class="badge" style="width:84px;height:84px;border-radius:50%"></div>
    <div class="badge" style="width:64px;height:84px;border-radius:32px"></div>
    <div class="badge" style="width:260px;height:80px;border-radius:8px"></div>
  </div>
</section>

<div class="abs tour-band"></div>
<section class="abs" style="left:107px;top:2236px;width:330px;color:#fff">
  <h2 style="color:#fff">Behind-the-<br>Scenes Tour</h2>
  <p class="body" style="color:#cfcfcf;margin-top:22px">Explore the specialized rooms and advanced equipment that bring every garment to life, from design to final quality checks.</p>
  <svg style="margin-top:34px" width="260" height="34" viewBox="0 0 260 34">
    <path d="M22 17H2M12 7L2 17l10 10" fill="none" stroke="#777" stroke-width="3"/>
    <line x1="52" y1="17" x2="70" y2="17" stroke="#fff" stroke-width="3"/>
    <line x1="76" y1="17" x2="205" y2="17" stroke="#888" stroke-width="2" stroke-dasharray="5 5"/>
    <path d="M218 17h36M242 5l12 12-12 12" fill="none" stroke="#fff" stroke-width="3"/>
  </svg>
</section>
<div class="photo" style="left:439px;top:2206px;width:569px;height:322px;background:linear-gradient(160deg,#d8d8d6,#9e9c98 60%,#6e6c68)" role="img" aria-label="Photo of the cutting room with an automated fabric cutting table"></div>
<div class="abs caption" style="left:856px;top:2474px;width:237px;height:75px">Cutting Room</div>

<section class="abs" style="left:107px;top:2602px">
  <div class="grid">
    <div style="padding-top:2px"><h2>Extra Benefits<br>for People</h2></div>
    <div class="card dark" style="height:216px">
      <svg class="icon" viewBox="0 0 24 24" fill="#fff"><path d="M5 2h2v7h1V2h2v7h1V2h2v8a3 3 0 0 1-3 3v9H8v-9a3 3 0 0 1-3-3zM17 2c2 0 3 3 3 7v4h-2v9h-2V2z"/></svg>
      <h3>Food Tickets</h3><p class="body">Enjoy meal vouchers to make lunchtime more affordable and convenient.</p></div>
    <div class="card" style="height:216px">
      <svg class="icon" viewBox="0 0 24 24"><circle cx="6" cy="6" r="3" fill="#222"/><circle cx="18" cy="18" r="3" fill="#222"/><path d="M19 4L5 20" stroke="#222" stroke-width="2.5"/></svg>
      <h3>Loyalty Cards With Discounts</h3><p class="body">Access exclusive discounts on groceries, healthcare, dining, and home materials at local facilities.</p></div>
    <div class="card" style="height:216px">
      <svg class="icon" viewBox="0 0 24 24" fill="#222"><path d="M8 3h8v3h5v15H3V6h5zm2 2v1h4V5zm1 5v3H8v2h3v3h2v-3h3v-2h-3v-3z"/></svg>
      <h3>Health Insurance &amp; Medical Services</h3><p class="body">Benefit from reimbursed health insurance and medical services for peace of mind and well-being.</p></div>
    <div class="card" style="height:216px">
      <svg class="icon" viewBox="0 0 24 24" fill="#222"><path d="M13 2l8 8-3 3-8-8zM9 6l8 8-2 2-8-8zM8 13l3 3-7 7-3-3z"/></svg>
      <h3>Legal Services For Employee</h3><p class="body">Get access to free legal assistance and support with our on-staff lawyer.</p></div>
    <div class="card" style="height:216px">
      <svg class="icon" viewBox="0 0 24 24" fill="#222"><path d="M6 2h12a3 3 0 0 1 3 3v13h-2v3h-3v-3H8v3H5v-3H3V5a3 3 0 0 1 3-3zm0 3v6h12V5zm1 8a1.5 1.5 0 1 0 0 3 1.5 1.5 0 0 0 0-3zm10 0a1.5 1.5 0 1 0 0 3 1.5 1.5 0 0 0 0-3z"/></svg>
      <h3>Paid Transportation For Employee</h3><p class="body">Comfortable and reliable transportation is provided to and from work at no cost to you.</p></div>
  </div>
</section>

<h2 class="abs" style="left:107px;top:3104px;width:986px;text-align:center">Community Activites</h2>
<div class="photo" style="left:107px;top:3178px;width:320px;height:377px;background:linear-gradient(170deg,#6e7a5a,#4a5040 60%,#3b3530)" role="img" aria-label="Photo of employees at the summer camp outdoors"></div>
<div class="photo" style="left:441px;top:3178px;width:320px;height:377px;background:linear-gradient(170deg,#8b8e90,#5d5f66 55%,#3e4048)" role="img" aria-label="Photo of employees in costumes at the Halloween party"></div>
<div class="photo" style="left:774px;top:3178px;width:319px;height:377px;background:linear-gradient(170deg,#c9c6c0,#8a857d 55%,#4e4a45)" role="img" aria-label="Photo of employees celebrating Christmas together"></div>
<div class="abs captions" style="left:107px;top:3570px">
  <span style="width:320px">Summer Camp</span><span style="width:320px">Halloween Party</span><span>Christmas Creativity</span>
</div>

<div class="photo" style="left:107px;top:3657px;width:486px;height:416px;background:linear-gradient(120deg,#dcdcdc,#9a9a9a 50%,#3a3a3a)" role="img" aria-label="Black and white photo of two models in hats and tailored clothing"></div>
<section class="abs" style="left:607px;top:3657px;width:486px">
  <h2 style="font-size:40px">Ready to Bring Your Designs to Life?</h2>
  <p class="body" style="margin-top:12px">Contact us today to get started on your next project.</p>
  <div style="display:flex;gap:14px;margin-top:24px">
    <div style="flex:1"><label>Your Name</label><div class="field" style="color:#222">John Doe</div></div>
    <div style="flex:1"><label>Email</label><div class="field">Enter your email</div></div>
  </div>
  <div style="margin-top:18px"><label>Message</label><div class="field" style="height:84px;border-radius:16px;align-items:flex-start;padding-top:12px">Tell us your idea</div></div>
  <div class="btn-dark" style="margin-top:22px;margin-left:348px;padding:13px 26px">Send Message</div>
</section>

<footer class="abs footer">
  <div class="abs" style="left:107px;top:52px;font-size:52px;font-weight:300;letter-spacing:-1px">Velmora</div>
  <div class="abs sm" style="left:107px;top:138px;width:260px">Strada Carpaților 48, Brăila 810012, Romania</div>
  <div class="abs sm" style="left:107px;top:186px">07:30 am - 4:00 pm</div>
  <div class="abs" style="left:607px;top:54px"><h4>Navigation</h4>
    <div class="sm" style="line-height:2.65">About Us<br>Strong Value<br>Expertise<br>Get in Touch</div></div>
  <div class="abs" style="left:856px;top:54px"><h4>Contact</h4>
    <div class="sm" style="line-height:2.65">
      <svg width="11" height="9" viewBox="0 0 11 9"><rect width="11" height="9" fill="#fff"/><path d="M0 0l5.5 4.5L11 0" fill="none" stroke="#23262b"/></svg>&nbsp; hello@velmoraatelier.com<br>
      <svg width="11" height="11" viewBox="0 0 24 24" fill="#fff"><path d="M6 2l4 5-2 3a12 12 0 0 0 6 6l3-2 5 4-3 4C10 22 2 14 2 5z"/></svg>&nbsp; +4(0) 339 205 118</div>
    <div style="display:flex;gap:16px;margin-top:18px">
      <span style="width:20px;height:20px;border-radius:50%;border:2px solid #fff"></span>
      <span style="width:20px;height:20px;border-radius:50%;border:2px solid #fff"></span>
      <span style="width:20px;height:20px;border-radius:50%;border:2px solid #fff"></span>
    </div></div>
  <div class="abs sm" style="left:107px;top:270px">Copyright © 2024 Velmora Brăila. All rights reserved.</div>
  <div class="abs sm" style="left:893px;top:266px">Language
    <span class="flag" style="background:#1d2a5a"></span><span class="flag" style="background:linear-gradient(90deg,#002b7f 33%,#fcd116 33% 66%,#ce1126 66%)"></span><span class="flag" style="background:linear-gradient(#aa151b 25%,#f1bf00 25% 75%,#aa151b 75%)"></span><span class="flag" style="background:linear-gradient(90deg,#0055a4 33%,#fff 33% 66%,#ef4135 66%)"></span>
  </div>
</footer>

</body>
</html>
```